Specialised investor in e-mobility and energy wants business card design

We need a business card design that fits our existing corporate design. <The look and feel must be 'sharp'/'clean', dynamic, communicate momentum, professionalism etc (as one would imagine from a firm in the financial sector). We like the idea of a reverse-side of the card that includes the logo, and the name and contact details on the other. We expect the deliverable to be whatever format might be required to be able to get cards printed directly by a service such as kelmo press. Our website is www.zub.capital

```html
<!DOCTYPE html>
<html lang="en">
<head>
<meta charset="utf-8">
<title>ZUB Capital – Business Card</title>
<link rel="stylesheet" href="https://fonts.googleapis.com/css2?family=Montserrat:wght@400;500;700&display=swap">
<style>
  :root {
    --backdrop: #e8e5e0;
    --card: #ffffff;
    --brand-dark: #2f5020;
    --brand-light: #7fb347;
    --text: #2a2a2a;
    --muted: #4a4a4a;
  }
  * { margin: 0; padding: 0; box-sizing: border-box; }
  html, body { width: 900px; height: 1200px; overflow: hidden; }
  body {
    position: relative;
    background: var(--backdrop);
    font-family: "Montserrat", Arial, sans-serif;
    color: var(--text);
  }
  .card {
    position: absolute;
    left: 80px;
    width: 742px;
    height: 440px;
    background: var(--card);
    border-radius: 40px;
    box-shadow: 0 4px 10px rgba(0,0,0,0.35);
  }
  .card--front { top: 132px; }
  .card--back { top: 638px; }

  .wordmark {
    position: absolute;
    display: flex;
    align-items: center;
    color: var(--brand-dark);
    font-weight: 500;
    white-space: nowrap;
  }
  .wordmark__dot {
    display: inline-block;
    border-radius: 50%;
    background: var(--brand-dark);
  }
  .card--front .wordmark { left: 28px; top: 226px; font-size: 42px; gap: 14px; }
  .card--front .wordmark__dot { width: 14px; height: 14px; }
  .card--back .wordmark { left: 0; right: 0; top: 190px; justify-content: center; font-size: 66px; gap: 20px; }
  .card--back .wordmark__dot { width: 20px; height: 20px; }

  .divider {
    position: absolute;
    left: 406px;
    top: 140px;
    width: 2px;
    height: 188px;
    background: var(--brand-light);
  }
  .contact { position: absolute; left: 461px; top: 138px; }
  .contact__name { font-size: 27px; font-weight: 700; color: var(--brand-dark); line-height: 32px; }
  .contact__role { font-size: 16px; color: var(--muted); line-height: 20px; padding-left: 2px; }
  .contact__list { list-style: none; margin-top: 22px; }
  .contact__item { display: flex; align-items: center; gap: 10px; font-size: 16px; line-height: 22px; }
  .contact__item svg { width: 14px; height: 14px; fill: var(--brand-light); flex: none; }
  .contact__address { margin-top: 14px; font-size: 16px; line-height: 21px; }
</style>
</head>
<body>
  <section class="card card--front">
    <div class="wordmark"><span class="wordmark__dot"></span>ZUB Capital</div>
    <div class="divider"></div>
    <div class="contact">
      <h1 class="contact__name">Peter Halloway</h1>
      <p class="contact__role">Owner</p>
      <ul class="contact__list">
        <li class="contact__item">
          <svg viewBox="0 0 16 16" aria-hidden="true"><path d="M2 6c0-2 3-3 6-3s6 1 6 3v1h-3V6H5v1H2zM4 8h8l1 6H3z"/></svg>
          +41 79555 0148
        </li>
        <li class="contact__item">
          <svg viewBox="0 0 16 16" aria-hidden="true"><path d="M1 4h14v9H1zM2 5l6 4 6-4v1L8 10 2 6z" fill-rule="evenodd"/></svg>
          peter@zub.capital
        </li>
        <li class="contact__item">
          <svg viewBox="0 0 16 16" aria-hidden="true"><circle cx="8" cy="8" r="7"/></svg>
          www.zub.capital.com
        </li>
      </ul>
      <p class="contact__address">48 Harlow Lane, Suite 210<br>Ridgefield, PA 18032</p>
    </div>
  </section>

  <section class="card card--back">
    <div class="wordmark"><span class="wordmark__dot"></span>ZUB Capital</div>
  </section>
</body>
</html>
```